FinTech company looking to revamp and expand client-facing interface for our financial models

Pellworth Engines currently has a very simple website that allows clients to interact with our financial models. We are looking to completely redesign the current site and add several extra pages to provide extra functionality. We want the design to have a modern, slick feel, that will work on both a desktop or a tablet. It should be straightforward for clients to move between different pages at any time, and clear from the layout how to interact with the more advanced features. We have included screenshots of existing pages in the attached design brief, as well as sketches of the functionality required by the new pages, but can't provide a direct link to the current site.
Target Market(s)
Professional investors that will be paying to access the interface
Industry/Entity Type
Finance
Number of Pages Required
4 page
Colors
Designer to choose colors to be used in the design.
Look and feel
Each slider illustrates characteristics of the customer's brand and the style your logo design should communicate.

```html
<!DOCTYPE html>
<html lang="en">
<head>
<meta charset="utf-8">
<title>Pellworth Engines – Models</title>
<link rel="stylesheet" href="https://fonts.googleapis.com/css2?family=Montserrat:wght@500;600;700&family=Roboto+Condensed:wght@400;500&family=Open+Sans:wght@400;600&display=swap">
<style>
:root{
  --frame:#e6e6e6;
  --white:#ffffff;
  --ink:#111111;
  --active:#9c9c9c;
  --navy:#003366;
  --link:#1e4aa8;
  --head-grey:#9a9a9a;
  --row-alt:#f4f4f4;
  --line:#dcdcdc;
}
*{box-sizing:border-box;margin:0;padding:0}
html,body{width:1200px;height:715px;overflow:hidden;background:var(--frame)}
body{font-family:"Montserrat",sans-serif;color:var(--ink)}
.app{position:absolute;left:14px;top:14px;width:1172px;height:687px;
  background:linear-gradient(180deg,#efefef 0px,#efefef 140px,#e9e9e9 160px,#fafafa 400px,#f4f4f4 100%);overflow:hidden}
.topbar{position:absolute;left:0;top:0;width:100%;height:55px;background:var(--white);display:flex;align-items:stretch}
.product{width:166px;display:flex;align-items:center;padding-left:52px;font-weight:600;font-size:16px}
.period{width:83px;display:flex;align-items:center;justify-content:center;font-weight:700;font-size:13px;border-right:1px solid #eee}
.period.is-active{background:var(--active);color:var(--white);border:none}
.spacer{flex:1;border-left:1px solid #eee}
.nav-item{display:flex;align-items:center;justify-content:center;gap:7px;font-weight:700;font-size:12.5px;border-left:1px solid #eee}
.nav-item svg{width:22px;height:22px}
.nav-item.is-active{background:var(--active);color:var(--white)}
.nav-models{width:129px}.nav-sens{width:164px}.nav-fav{width:182px}

.tabs{position:absolute;left:30px;top:92px;display:flex;gap:5px}
.tab{width:143px;height:51px;background:var(--white);border-radius:5px 5px 0 0;display:flex;flex-direction:column;align-items:center;justify-content:center;gap:4px;font-size:12px;font-weight:600;color:#444}
.tab svg{width:18px;height:18px}
.tab-more{width:37px}
.tab-add{width:37px;background:var(--navy);border-radius:5px 5px 0 0;height:51px;display:flex;align-items:center;justify-content:center}
.band{position:absolute;left:0;top:143px;width:100%;height:260px;background:linear-gradient(180deg,#e4e4e4,rgba(244,244,244,0))}

.filters{position:absolute;left:52px;top:190px;display:flex;align-items:center;font-family:"Open Sans",sans-serif;font-size:16px;width:1086px}
.filters b{font-weight:600}
.label-gap{margin-left:28px}
.label-gap-sm{margin-left:12px}
.filters input{width:166px;height:28px;border:1px solid #ccc;border-radius:4px;margin-left:14px;padding-left:10px;font-family:"Open Sans",sans-serif;font-size:15.5px;background:var(--white)}
.filter-gap{width:40px}
.export{margin-left:auto;display:flex;align-items:center;gap:7px;color:var(--link);font-family:"Open Sans",sans-serif;font-weight:600;font-size:16px;text-decoration:none}

.models{position:absolute;left:51px;top:244px;width:1070px;border-collapse:separate;border-spacing:0;background:var(--white);border-radius:6px;box-shadow:0 2px 8px rgba(0,0,0,.18);overflow:hidden;table-layout:fixed}
.models th{height:64px;font-weight:600;font-size:15.5px;color:var(--white);background:var(--head-grey);border-right:1px solid #b3b3b3}
.models th.key{background:var(--navy);border-right:1px solid #2b5280}
.models th:last-child{border-right:none}
.models td{height:64px;font-family:"Roboto Condensed",sans-serif;font-size:16px;text-align:center;border-right:1px solid var(--line);border-top:1px solid var(--line);line-height:1.2}
.models td:last-child{border-right:none}
.models td.sector{text-align:left;padding-left:9px}
.models tr:nth-child(even) td{background:var(--row-alt)}
.models td.num{text-align:left;padding-left:8px}
</style>
</head>
<body>
<div class="app">
  <header class="topbar">
    <div class="product">Pellworth</div>
    <div class="period is-active">250D</div>
    <div class="period">83D</div>
    <div class="period">42D</div>
    <div class="spacer"></div>
    <div class="nav-item nav-models is-active">
      <svg viewBox="0 0 24 24" fill="none" stroke="#fff" stroke-width="1.8"><path d="M3 11l9-8 9 8"/><path d="M5 10v10h5v-6h4v6h5V10"/></svg>MODELS</div>
    <div class="nav-item nav-sens">
      <svg viewBox="0 0 24 24" fill="#222"><circle cx="12" cy="12" r="3"/><circle cx="12" cy="3" r="1.6"/><circle cx="12" cy="21" r="1.6"/><circle cx="3" cy="12" r="1.6"/><circle cx="21" cy="12" r="1.6"/><circle cx="5.6" cy="5.6" r="1.6"/><circle cx="18.4" cy="18.4" r="1.6"/><circle cx="18.4" cy="5.6" r="1.6"/><circle cx="5.6" cy="18.4" r="1.6"/></svg>SENSITIVITIES</div>
    <div class="nav-item nav-fav">
      <svg viewBox="0 0 24 24" fill="none" stroke="#111" stroke-width="1.6"><path d="M12 2.5l2.9 6.2 6.6.7-5 4.5 1.4 6.6L12 17.2l-5.9 3.3 1.4-6.6-5-4.5 6.6-.7z"/></svg>FAVOURITES</div>
  </header>

  <div class="band"></div>

  <nav class="tabs">
    <div class="tab"><svg viewBox="0 0 20 20" fill="#555"><rect x="2" y="4" width="16" height="2"/><rect x="2" y="9" width="16" height="2"/><rect x="2" y="14" width="16" height="2"/></svg>EQUITIES</div>
    <div class="tab"><svg viewBox="0 0 20 20" fill="#555"><rect x="3" y="12" width="3" height="6"/><rect x="8" y="9" width="3" height="9"/><rect x="13" y="6" width="3" height="12"/><path d="M3 9l5-4 4 2 5-5" stroke="#555" stroke-width="1.5" fill="none"/></svg>ETFS</div>
    <div class="tab"><svg viewBox="0 0 20 20" fill="none" stroke="#555" stroke-width="1.6"><circle cx="10" cy="10" r="7"/><circle cx="10" cy="10" r="3"/><path d="M10 10l7-7"/></svg>PAIRS</div>
    <div class="tab"><svg viewBox="0 0 20 20" fill="none" stroke="#555" stroke-width="1.5"><rect x="4" y="2" width="12" height="16" rx="1"/><path d="M7 7h6M7 10h6M7 13h6"/></svg>ETF PAIRS</div>
    <div class="tab"><svg viewBox="0 0 20 20" fill="#555"><path d="M6 4l7-2v16l-7 2z"/></svg>FACTORS</div>
    <div class="tab"><svg viewBox="0 0 20 20" fill="none" stroke="#777" stroke-width="1.2"><path d="M3 3l14 14M17 3L3 17M10 2v16M2 10h16"/></svg>NEW TAB TITLE #1</div>
    <div class="tab"><svg viewBox="0 0 20 20" fill="none" stroke="#555" stroke-width="1.4"><circle cx="5" cy="14" r="2.5"/><circle cx="10" cy="9" r="2.5"/><circle cx="15" cy="6" r="2.5"/></svg>NEW TAB TITLE #2</div>
    <div class="tab tab-more"><svg viewBox="0 0 20 20" fill="none" stroke="#777" stroke-width="2.2"><path d="M7 4l6 6-6 6"/></svg></div>
    <div class="tab-add"><svg width="20" height="20" viewBox="0 0 20 20" fill="none" stroke="#fff" stroke-width="1.6"><circle cx="10" cy="10" r="8.5"/><path d="M10 5v10M5 10h10"/></svg></div>
  </nav>

  <div class="filters">
    <span>Quality</span><b class="label-gap">Threshold:</b><input type="text" value="-10">
    <span class="filter-gap"></span>
    <span><b>Abs.</b> Stat</span><b class="label-gap-sm">Threshold:</b><input type="text" value="-10">
    <a class="export" href="#"><svg width="24" height="22" viewBox="0 0 24 22" fill="none" stroke="#1e4aa8" stroke-width="2"><path d="M10 5H4a2 2 0 0 0-2 2v11a2 2 0 0 0 2 2h12a2 2 0 0 0 2-2v-5"/><path d="M9 14c1-5 5-8 11-8M16 2l5 4-5 4"/></svg>Export</a>
  </div>

  <table class="models">
    <colgroup><col style="width:92px"><col style="width:102px"><col style="width:106px"><col style="width:106px"><col span="8" style="width:83px"></colgroup>
    <thead><tr>
      <th class="key">ID <svg width="11" height="8" viewBox="0 0 11 8" fill="none" stroke="#fff" stroke-width="2"><path d="M1 1l4.5 4.5L10 1"/></svg></th>
      <th class="key">Sector</th><th class="key">Time</th>
      <th>Quality</th><th>Stat 1</th><th>Stat 2</th><th>Stat 3</th><th>Stat 4</th><th>Stat 5</th><th>Stat 6</th><th>Stat 7</th><th>Stat 8</th>
    </tr></thead>
    <tbody>
      <tr><td>Model 1</td><td class="sector">Materials</td><td>2019-07-03<br>12:15:00.000</td><td>30.2288</td><td class="num">2.01574</td><td class="num">23.305</td><td class="num">-0.149368</td><td class="num">22.3054</td><td class="num">4.63714</td><td class="num">0.945706</td><td class="num">2.81949</td><td class="num">2.60858</td></tr>
      <tr><td>Model 2</td><td class="sector">Industrials</td><td>2019-07-03<br>12:15:00.000</td><td>32.8694</td><td class="num">0.87307</td><td class="num">32.185</td><td class="num">-0.033692</td><td class="num">33.9911</td><td class="num">11.5693</td><td class="num">-0.472968</td><td class="num">-0.830458</td><td class="num">6.80646</td></tr>
      <tr><td>Model 3</td><td class="sector">Consumer<br>Discretionary</td><td>2019-07-03<br>12:15:00.000</td><td>1.66002</td><td class="num">-0.569222</td><td class="num">159.814</td><td class="num">0.0252328</td><td class="num">172.616</td><td class="num">10.2875</td><td class="num">-0.750396</td><td class="num">-0.385309</td><td class="num">4.69146</td></tr>
      <tr><td>Model 4</td><td class="sector">Information<br>Technology</td><td>2019-07-03<br>12:15:00.000</td><td>45.6856</td><td class="num">0.412148</td><td class="num">202.488</td><td class="num">0.0084923</td><td class="num">205.834</td><td class="num">11.9094</td><td class="num">-0.137913</td><td class="num">0.449595</td><td class="num">3.85106</td></tr>
      <tr><td>Model 5</td><td class="sector">Information<br>Technology</td><td>2019-07-03<br>12:15:00.000</td><td>75.7733</td><td class="num">7.06728</td><td class="num">188.605</td><td class="num">0.016913</td><td class="num">161.665</td><td class="num">3.82241</td><td class="num">0.981019</td><td class="num">1.29847</td><td class="num">3.34927</td></tr>
    </tbody>
  </table>
</div>
</body>
</html>
```